Wordpress Design Project (Nerith)

We need a wordpress design for an established auction and real estate company based in Pennsylvania. The winning design will incorporate a professional layout with and company logo in a very simple and clean layout.

Industry/Entity Type

Real Estate

Requirements
Must have
• Navigation:
1) Home; 2) Auctions; 3) Appraisals; 4) Real Estate; 5) FAQ; 6) About Us; 7) Contact Us.

Site will have overall layout of https://www.plumvarro.com/featured/regions/the-northeast. Home page will have logo and navigation at top. The navigation bar will also have social media icons (facebook, Google+, RSS, twitter) inside it. There will be text in the content area - use lorem ipsum. The image attached will be used below text (auctions.jpg) . Footer will have smaller company loogo, the attached affiliation logos and social media icons.

Logo attached. Color scheme will be black, gray, and red as accent color.
Nice to have
• navigation will have dropdowns, nice to have one represented - under auctions 'All Auctions' will be dropdown.

```html
<!DOCTYPE html>
<html lang="en">
<head>
<meta charset="utf-8">
<title>Nerith Auctioneers &amp; Appraisers</title>
<link href="https://fonts.googleapis.com/css2?family=PT+Sans:wght@400;700&family=PT+Sans+Narrow:wght@700&display=swap" rel="stylesheet">
<style>
:root{
  --red:#d0262b;
  --red-dark:#b01d22;
  --ink:#1a1a1a;
  --text:#555;
  --muted:#777;
  --bar:#353535;
  --band:#f1f1f1;
  --rule:#dcdcdc;
  --white:#fff;
}
*{box-sizing:border-box;margin:0;padding:0}
html,body{width:926px;height:1200px;overflow:hidden;background:var(--white)}
body{position:relative;font-family:"PT Sans",Arial,sans-serif;color:var(--text)}
.abs{position:absolute}
.cond{font-family:"PT Sans Narrow","Arial Narrow",sans-serif;font-weight:700}

.topbar{left:0;top:0;width:926px;height:20px;background:var(--bar)}
.topbar .phone{left:92px;top:4px;display:flex;align-items:center;gap:6px;color:#bbb;font-size:8.5px;letter-spacing:.2px}
.topbar .search-tab{left:639px;top:3px;width:196px;height:30px;background:var(--white);border-radius:2px 2px 0 0;padding:6px 8px}
.search-field{width:100%;height:100%;border:1px solid #ddd;background:#f7f7f7;display:flex;justify-content:flex-end;align-items:center;padding-right:5px}

.header{left:0;top:20px;width:926px;height:75px;background:linear-gradient(#f9f9f9,#ececec);border-bottom:2px solid #d8d8d8}
.brand{left:92px;top:11px;display:flex;align-items:center;gap:8px}
.brand .mark{width:52px;height:52px;background:var(--red);border-radius:4px}
.brand .name{font-size:34px;color:var(--ink);font-weight:700;letter-spacing:.5px}
.nav{left:334px;top:28px;display:flex;align-items:center;font-size:10px;color:#333}
.nav a{color:inherit;text-decoration:none;padding:5px 12px;margin-right:10px}
.nav a.current{background:var(--red);color:var(--white)}

.hero{left:0;top:95px;width:926px;height:292px;background:linear-gradient(90deg,#ececec,#f1f1f1)}
.hero .visual{left:418px;top:6px;width:508px;height:286px;background:radial-gradient(ellipse at 55% 55%,#e9c9a4 0%,#dcb48a 35%,#efe4d8 70%,#f1f1f1 100%)}
.hero h1{left:92px;top:52px;font-size:35px;color:var(--red);letter-spacing:-.3px}
.hero h2{left:92px;top:91px;font-size:19px;color:var(--red)}
.hero p{left:92px;top:121px;width:320px;font-size:10px;line-height:13px}
.btn-view{left:92px;top:179px;width:101px;height:29px;background:linear-gradient(#7d7d7d,#5c5c5c);border:1px solid #444;border-radius:2px;color:#eee;font-size:15px;display:flex;align-items:center;justify-content:center}
.dots{left:92px;top:240px;display:flex;gap:4px}
.dots span{width:7px;height:7px;border-radius:50%;background:#999;border:1px solid #777}
.dots span.on{background:#333}
.hero .search{left:637px;top:132px;width:194px;height:26px;background:var(--white);border:1px solid #ddd;border-radius:2px;display:flex;justify-content:flex-end;align-items:center}
.hero .search .sep{width:1px;height:18px;background:#ddd;margin-right:9px}

.welcome{left:92px;top:388px;width:742px;text-align:center}
.welcome h2{font-size:37px;color:var(--ink);line-height:40px}
.welcome h3{font-size:19px;color:#555;margin-top:4px}
.welcome p{font-size:10px;line-height:13px;margin-top:6px}
.rule{height:1px;background:var(--rule)}

.card{width:363px}
.card .photo{width:363px;height:169px}
.card .meta{position:relative;height:53px;border-bottom:1px solid var(--rule);padding-top:8px}
.card h4{font-size:11px;color:var(--red)}
.card .desc{font-size:10px;margin-top:1px}
.card .date{font-size:8.5px;color:var(--red);font-weight:700;margin-top:1px}
.card .loc{position:absolute;right:0;top:14px;display:flex;align-items:center;gap:6px;font-size:8.5px;color:#444}

.subscribe h3{font-size:19px;color:#333}
.subscribe p{font-size:10px;line-height:13px;width:240px}
.email{left:338px;top:1023px;width:383px;height:31px;border:2px solid #ccc;border-radius:2px;font-size:10px;color:#666;padding:7px 5px}
.btn-sub{left:737px;top:1023px;width:97px;height:31px;background:var(--red);border:1px solid var(--red-dark);border-radius:2px;color:var(--white);font-size:13px;display:flex;align-items:center;justify-content:center}

.affil-title{left:146px;top:1099px;font-size:23px;color:#888;letter-spacing:.5px}
.badge{background:#cfcfcf}

.footer{left:0;top:1155px;width:926px;height:45px;background:var(--band);border-top:1px solid #ddd}
.footer .links{left:92px;top:12px;font-size:8.5px;line-height:14px;color:#666}
.social{left:705px;top:12px;display:flex;gap:6px}
.social span{width:21px;height:21px}
</style>
</head>
<body>

<div class="abs topbar">
  <div class="abs phone">
    <svg width="10" height="10" viewBox="0 0 10 10"><path d="M2 0.5 L3.6 2.8 L2.8 3.8 Q4 6 6.2 7.2 L7.2 6.4 L9.5 8 L8.4 9.5 Q4.5 9.3 0.5 1.6Z" fill="#bbb"/></svg>
    CALL US ON (000) 000 000
  </div>
  <div class="abs search-tab"><div class="search-field">
    <svg width="9" height="9" viewBox="0 0 9 9"><circle cx="3.5" cy="3.5" r="2.6" stroke="#bbb" fill="none"/><path d="M5.5 5.5L8.5 8.5" stroke="#bbb" stroke-width="1.4"/></svg>
  </div></div>
</div>

<header class="abs header">
  <div class="abs brand"><span class="mark"></span><span class="name">Nerith</span></div>
  <nav class="abs nav">
    <a class="current">Home</a><a>Auctions</a><a>Appraisals</a><a>Real Estate</a><a>FAQ</a><a>About Us</a><a>Contact Us</a>
  </nav>
</header>

<section class="abs hero">
  <div class="abs visual" role="img" aria-label="Wooden house cut-out standing on assembled wooden jigsaw puzzle pieces"></div>
  <h1 class="abs cond">LOREM IPSUM DOLOR SIT</h1>
  <h2 class="abs cond">AMET, CONSECTETUR ADIPISIC</h2>
  <p class="abs">sed do eiusmod tempor incididunt ut labore et dolore magna aliqua. Ut enim ad minim veniamsed do eiusmod tempor incididunt ut labore et dolore magna aliqua. Ut enim ad minim veniam</p>
  <div class="abs btn-view cond">VIEW AUCTIONS</div>
  <div class="abs dots"><span></span><span></span><span class="on"></span><span></span><span></span><span></span></div>
  <div class="abs search"><span class="sep"></span>
    <svg width="9" height="9" viewBox="0 0 9 9" style="margin-right:8px"><circle cx="3.5" cy="3.5" r="2.6" stroke="#bbb" fill="none"/><path d="M5.5 5.5L8.5 8.5" stroke="#bbb" stroke-width="1.4"/></svg>
  </div>
</section>

<section class="abs welcome">
  <h2 class="cond">WELCOME TO</h2>
  <h3 class="cond">NERITH AUCTIONEER &amp; APPRAISERS</h3>
  <p>sed do eiusmod tempor incididunt ut labore et dolore magna aliqua. Ut enim ad minim veniamsed do eiusmod tempor incididunt ut labore et dolore magna aliqua. Ut enim ad minim veniame et dolore magna aliqua. Ut enim ad minim veniamsed do eiusmod tempor incididunt ut labore et dolore magna aliqua. Ut enim ad minim veniam</p>
</section>
<div class="abs rule" style="left:92px;top:510px;width:742px"></div>

<article class="abs card" style="left:92px;top:526px">
  <div class="photo" role="img" aria-label="Rolls of carpet with yellow lot tags in a warehouse" style="background:linear-gradient(135deg,#8d8a85,#b3aca3 50%,#6f6a63)"></div>
  <div class="meta"><h4 class="cond">PERSPICIATIS UNDE OMNIS ISTE NATUS ERROR SIT</h4><p class="desc">sed do eiusmod tempor incididunt ut</p><p class="date">10 August, 2013</p>
    <div class="loc"><svg width="12" height="16" viewBox="0 0 12 16"><path d="M6 0.5a5.5 5.5 0 0 1 5.5 5.5C11.5 10 6 15.5 6 15.5S0.5 10 0.5 6A5.5 5.5 0 0 1 6 0.5z" fill="var(--red)"/><circle cx="6" cy="6" r="2.2" fill="#fff"/></svg>Brackett Cove, ME</div></div>
</article>
<article class="abs card" style="left:470px;top:526px">
  <div class="photo" role="img" aria-label="Row of white paneled doors with windows lined up for auction" style="background:linear-gradient(90deg,#b9c6cf,#dfe4e6 45%,#c9c2b0 80%,#a57c4f)"></div>
  <div class="meta"><h4 class="cond">PERSPICIATIS UNDE OMNIS ISTE NATUS ERROR SIT</h4><p class="desc">sed do eiusmod tempor incididunt ut</p><p class="date">10 August, 2013</p>
    <div class="loc"><svg width="12" height="16" viewBox="0 0 12 16"><path d="M6 0.5a5.5 5.5 0 0 1 5.5 5.5C11.5 10 6 15.5 6 15.5S0.5 10 0.5 6A5.5 5.5 0 0 1 6 0.5z" fill="var(--red)"/><circle cx="6" cy="6" r="2.2" fill="#fff"/></svg>Brackett Cove, ME</div></div>
</article>
<article class="abs card" style="left:92px;top:764px">
  <div class="photo" role="img" aria-label="Wooden bathroom vanities with dark stone tops and sinks" style="background:linear-gradient(160deg,#c9a77f,#a4622a 45%,#3b2a22 70%,#8a5428)"></div>
  <div class="meta"><h4 class="cond">PERSPICIATIS UNDE OMNIS ISTE NATUS ERROR SIT</h4><p class="desc">sed do eiusmod tempor incididunt ut</p><p class="date">10 August, 2013</p>
    <div class="loc"><svg width="12" height="16" viewBox="0 0 12 16"><path d="M6 0.5a5.5 5.5 0 0 1 5.5 5.5C11.5 10 6 15.5 6 15.5S0.5 10 0.5 6A5.5 5.5 0 0 1 6 0.5z" fill="var(--red)"/><circle cx="6" cy="6" r="2.2" fill="#fff"/></svg>Brackett Cove, ME</div></div>
</article>
<article class="abs card" style="left:470px;top:764px">
  <div class="photo" role="img" aria-label="Rows of cherry wood kitchen cabinets with yellow lot tags" style="background:linear-gradient(90deg,#c59a63,#7a2a1c 40%,#5e1c16 70%,#8a6a4a)"></div>
  <div class="meta"><h4 class="cond">PERSPICIATIS UNDE OMNIS ISTE NATUS ERROR SIT</h4><p class="desc">sed do eiusmod tempor incididunt ut</p><p class="date">10 August, 2013</p>
    <div class="loc"><svg width="12" height="16" viewBox="0 0 12 16"><path d="M6 0.5a5.5 5.5 0 0 1 5.5 5.5C11.5 10 6 15.5 6 15.5S0.5 10 0.5 6A5.5 5.5 0 0 1 6 0.5z" fill="var(--red)"/><circle cx="6" cy="6" r="2.2" fill="#fff"/></svg>Brackett Cove, ME</div></div>
</article>

<section class="abs subscribe" style="left:92px;top:1015px">
  <h3 class="cond">I WANT MORE STUFF LIKE THIS!</h3>
  <p>Subscribe and never miss out on finds &amp; deals delivered to your inbox.</p>
</section>
<div class="abs email">enter your email address</div>
<div class="abs btn-sub cond">SUBSCRIBE NOW!</div>

<div class="abs rule" style="left:92px;top:1080px;width:742px"></div>
<div class="abs affil-title">AFFILIATIONS</div>
<div class="abs badge" style="left:335px;top:1092px;width:33px;height:38px;border-radius:3px"></div>
<div class="abs badge" style="left:397px;top:1090px;width:58px;height:44px;border-radius:50%"></div>
<div class="abs badge" style="left:481px;top:1093px;width:42px;height:42px;border-radius:50%"></div>
<div class="abs badge" style="left:548px;top:1094px;width:34px;height:34px;border-radius:3px"></div>
<div class="abs badge" style="left:620px;top:1089px;width:36px;height:38px;border-radius:3px"></div>
<div class="abs badge" style="left:692px;top:1090px;width:60px;height:40px;border-radius:50%"></div>

<footer class="abs footer">
  <div class="abs links">Home | Auctions | Appraisals | Real Estate | FAQ | About Us | Contact Us<br>© 2013 Nerith | Privacy Policy | Terms</div>
  <div class="abs social">
    <span style="background:#3b5a9a"></span><span style="background:#2aa9e0"></span><span style="background:#f2922a"></span><span style="background:#cc2222"></span><span style="background:#333"></span>
  </div>
</footer>

</body>
</html>
```